The Lantern Guild Pitchdeck Template

The Lantern Guild would like a branded pitch deck template design for members to use when presenting their projects and proposals. The deck should include 10-15 different slide designs, each with the same branded theme, but with a variety of icon graphics and other design features that will empower members to easily create a beautiful pitch deck just by adding written content.

Please visit lanternguildhq.org to get a sense for our branding - purple, space, galaxy, white font and the planetary logo are some commonalities.

Here are 2 google drive links with some additional designs

https://files.boxmeadow.net/share/f/8QzrTa2Lk5VbNw7cHyP0dJe3sUmXg4RiF

https://files.boxmeadow.net/share/f/3Kd9-Rm6Tq2-yLvBn051fopwxhcT_zj7

```html
<!DOCTYPE html>
<html lang="en">
<head>
<meta charset="utf-8">
<title>The Lantern Guild – Pitch Deck Template</title>
<link href="https://fonts.googleapis.com/css2?family=Montserrat:wght@300;400;600;700;800&display=swap" rel="stylesheet">
<style>
:root{
  --page:#ececee;
  --white:#ffffff;
  --ink:#1d1d24;
  --muted:#6b6b76;
  --violet-deep:#1a1033;
  --violet:#4a2a8c;
  --violet-bright:#7b4fd6;
  --night:#0e0f1a;
  --rock:#3a3530;
  --lava:#d9531e;
  --panel:rgba(20,20,28,.78);
}
*{box-sizing:border-box;margin:0;padding:0}
html,body{width:1200px;height:3924px;overflow:hidden;background:var(--page);font-family:"Montserrat",sans-serif;color:var(--ink)}
.deck{position:relative;width:1200px;height:3924px}
.slide{position:absolute;left:104px;width:992px;height:560px;overflow:hidden;box-shadow:0 2px 10px rgba(0,0,0,.18)}
.s1{top:72px}.s2{top:704px}.s3{top:1336px}.s4{top:1968px}.s5{top:2600px}.s6{top:3232px}
.fill{position:absolute;inset:0}
.page-no{position:absolute;right:18px;bottom:16px;width:22px;height:22px;border-radius:50%;background:var(--white);color:var(--ink);font-size:10px;font-weight:600;display:flex;align-items:center;justify-content:center}
.brand{position:absolute;display:flex;align-items:center;gap:10px;color:var(--white);font-weight:300;letter-spacing:.14em;text-transform:uppercase}
.brand-dot{border:2px solid currentColor;border-radius:50%}
.brand.small{left:24px;top:18px;font-size:18px}
.brand.small .brand-dot{width:14px;height:14px}
.brand.dark{color:var(--ink)}
.title{font-weight:800;text-transform:uppercase;letter-spacing:.02em}

/* cover */
.s1 .fill{background:radial-gradient(ellipse at 30% 30%,#6b3fb8 0%,#2c1a5e 40%,#0b0a22 85%)}
.s1 .brand{left:0;right:0;top:238px;justify-content:center;font-size:54px}
.s1 .brand .brand-dot{width:30px;height:30px}

/* who are we */
.s2 .fill{background:linear-gradient(160deg,#5a5048 0%,#2d2824 40%,#6e2b12 62%,#e0641e 66%,#3a2f28 72%,#4d463f 100%)}
.s2 .frame{position:absolute;left:110px;top:118px;width:360px;height:372px;border:3px solid var(--white)}
.s2 .card{position:absolute;left:96px;top:104px;width:360px;height:372px;background:var(--white);padding:34px 30px}
.s2 .card h2{font-size:30px;margin-bottom:16px}
.body{font-size:9.5px;line-height:1.6;color:var(--muted)}
.body p+p{margin-top:10px}
.socials{display:flex;gap:10px;margin-top:18px}
.socials span{width:22px;height:22px;border-radius:50%;background:#4f63c9}

/* envision */
.s3 .fill{background:linear-gradient(135deg,#4a4644 0%,#1f1d1c 45%,#34302d 70%,#5b5550 100%)}
.s3 .title{position:absolute;right:26px;top:18px;color:var(--white);font-size:26px}
.grid3{position:absolute;left:118px;top:112px;width:756px;height:360px;display:grid;grid-template-columns:repeat(3,1fr);grid-template-rows:repeat(2,1fr)}
.cell-text{background:var(--white);padding:28px 24px;text-align:center}
.cell-text h3{font-size:12px;font-weight:700;margin-bottom:10px;text-transform:uppercase}
.cell-text p{font-size:8.5px;line-height:1.6;color:var(--muted)}
.ph-field{background:linear-gradient(180deg,#8e7bd6 0%,#5b49a8 55%,#6a4b9c 100%)}
.ph-bird{background:linear-gradient(180deg,#f2a33a 0%,#c8581c 55%,#3a1f14 100%)}
.ph-earth{background:radial-gradient(circle at 50% 50%,#3f86c9 0%,#2a5aa0 35%,#6b3fb8 60%,#22154a 100%)}

/* intentions */
.s4 .left{position:absolute;left:0;top:0;width:456px;height:560px;background:var(--white);padding:30px 34px}
.s4 .brand.small{position:static;font-size:22px}
.s4 h2{font-size:30px;margin:96px 0 16px}
.s4 .right{position:absolute;left:456px;top:0;width:536px;height:560px;background:radial-gradient(ellipse at 55% 45%,#3b5fa8 0%,#1b2a5a 35%,#0b0f22 80%)}
.s4 .link{margin-top:12px;font-size:8px;color:var(--muted)}

/* partners */
.s5 .fill{background:linear-gradient(160deg,#45403c 0%,#1c1a19 50%,#3b3733 100%)}
.s5 .title{position:absolute;right:26px;top:18px;color:var(--white);font-size:26px}
.grid4{position:absolute;left:40px;top:114px;width:908px;height:398px;display:grid;grid-template-columns:repeat(4,1fr);grid-template-rows:repeat(2,1fr)}
.tile{position:relative;display:flex;flex-direction:column;align-items:center;justify-content:center;gap:14px}
.tile .badge{width:70px;height:70px}
.tile .label{font-size:9px;font-weight:600;text-transform:uppercase;letter-spacing:.06em}
.t-violet{background:linear-gradient(135deg,#5b2fa8,#1c103f);color:var(--white)}
.t-dark{background:#15151c;color:var(--white)}
.t-black{background:#000;color:var(--white)}
.t-white{background:var(--white);color:var(--ink)}
.t-navy{background:#1a1f4a;color:var(--white)}
.t-grey{background:#e8e8ea;color:var(--ink)}

/* contact */
.s6 .fill{background:linear-gradient(180deg,#3a2a66 0%,#8a3f7a 38%,#e07a4a 62%,#6b2c2a 80%,#2a1416 100%)}
.s6 .panel{position:absolute;left:218px;top:148px;width:556px;height:260px;background:var(--panel);padding:38px 40px}
.s6 .brand{position:static;justify-content:center;font-size:42px}
.s6 .brand .brand-dot{width:24px;height:24px}
.contacts{display:grid;grid-template-columns:repeat(3,1fr);margin-top:44px;text-align:center;color:var(--white)}
.contacts .icon{width:30px;height:30px;border-radius:50%;background:var(--white);margin:0 auto 8px;display:flex;align-items:center;justify-content:center}
.contacts h4{font-size:9px;font-weight:700;text-transform:uppercase;letter-spacing:.06em}
.contacts p{font-size:8.5px;margin-top:3px;line-height:1.4}
</style>
</head>
<body>
<main class="deck">

  <section class="slide s1">
    <div class="fill" role="img" aria-label="Purple galaxy nebula with a glowing network of stars"></div>
    <div class="brand"><span class="brand-dot"></span>Lantern Guild</div>
    <span class="page-no">1</span>
  </section>

  <section class="slide s2">
    <div class="fill" role="img" aria-label="Dark volcanic rock split by a glowing lava crack"></div>
    <div class="brand small"><span class="brand-dot"></span>Lantern Guild</div>
    <div class="frame"></div>
    <div class="card">
      <h2 class="title">Who Are We</h2>
      <div class="body">
        <p>The Lantern Guild is a collective of makers, thinkers and guides who share one aim: to help people and projects grow in harmony with each other and with the wider world. We gather ideas, tools and people around a clear purpose.</p>
        <p>Members, partners, friends and supporters join our open network to share their work, learn together and shape a brighter common future.</p>
        <p>Join us on our channels below.</p>
      </div>
      <div class="socials" aria-label="Chat and Relay channels"><span></span><span></span></div>
    </div>
    <span class="page-no">2</span>
  </section>

  <section class="slide s3">
    <div class="fill" role="img" aria-label="Dark rocky mountain landscape"></div>
    <div class="brand small"><span class="brand-dot"></span>Lantern Guild</div>
    <h2 class="title">What We Envision</h2>
    <div class="grid3">
      <div class="ph-field" role="img" aria-label="Two children walking through a lavender field"></div>
      <div class="cell-text"><h3>Planet</h3><p>A world that lives in harmony with nature, where every being thrives on a healthy Earth.</p></div>
      <div class="ph-bird" role="img" aria-label="Eagle flying against a golden sunset"></div>
      <div class="cell-text"><h3>People</h3><p>A world that meets the needs of every person, giving each a safe base for growth and self-realization.</p></div>
      <div class="ph-earth" role="img" aria-label="Planet Earth seen from space"></div>
      <div class="cell-text"><h3>Peace</h3><p>A world where trust and care replace fear, and where every voice has a place at the table.</p></div>
    </div>
    <span class="page-no">3</span>
  </section>

  <section class="slide s4">
    <div class="left">
      <div class="brand small dark"><span class="brand-dot"></span>Lantern Guild</div>
      <h2 class="title">Intentions</h2>
      <div class="body">
        <p>The Lantern Guild brings together people and projects who want to build a fair and caring future. We share knowledge, tools and resources so that good ideas can take root and grow. Our members work across art, science, learning, health and community, and each brings a unique light to the whole.</p>
        <p>We intend to support open collaboration, honest exchange and steady growth, so that every member can find partners, funding and the space to create lasting change.</p>
      </div>
      <p class="link">Find more at lanternguildhq.org</p>
    </div>
    <div class="right" role="img" aria-label="Hand holding a glowing glass capsule in deep space"></div>
    <span class="page-no">4</span>
  </section>

  <section class="slide s5">
    <div class="fill" role="img" aria-label="Dark rocky landscape"></div>
    <div class="brand small"><span class="brand-dot"></span>Lantern Guild</div>
    <h2 class="title">Partners</h2>
    <div class="grid4">
      <div class="tile t-violet"><svg class="badge" viewBox="0 0 70 70"><circle cx="35" cy="35" r="30" fill="none" stroke="#fff" stroke-width="3"/></svg><span class="label">Lantern Guild</span></div>
      <div class="tile t-dark"><svg class="badge" viewBox="0 0 70 70"><circle cx="35" cy="35" r="30" fill="#3fbf5a"/></svg><span class="label">Sproutline</span></div>
      <div class="tile t-black"><svg class="badge" viewBox="0 0 70 70"><rect x="6" y="6" width="58" height="58" fill="#e0d84a"/></svg><span class="label">Kindred Circle</span></div>
      <div class="tile t-dark"><svg class="badge" viewBox="0 0 70 70"><circle cx="35" cy="35" r="30" fill="#6a8fe0"/></svg><span class="label">Honeycomb Network</span></div>
      <div class="tile t-white"><svg class="badge" viewBox="0 0 70 70"><circle cx="35" cy="35" r="30" fill="#2aa6c9"/></svg><span class="label">Mycel</span></div>
      <div class="tile t-navy"><svg class="badge" viewBox="0 0 70 70"><circle cx="35" cy="35" r="30" fill="#4b3fd0"/></svg><span class="label">Endpoint</span></div>
      <div class="tile t-grey"><svg class="badge" viewBox="0 0 70 70"><rect x="6" y="6" width="58" height="58" fill="#3a3a44"/></svg><span class="label">Common Loom</span></div>
      <div class="tile t-black"><svg class="badge" viewBox="0 0 70 70"><circle cx="35" cy="35" r="30" fill="none" stroke="#fff" stroke-width="3"/></svg><span class="label">Lantern Guild</span></div>
    </div>
    <span class="page-no">5</span>
  </section>

  <section class="slide s6">
    <div class="fill" role="img" aria-label="Alien desert at sunset with planets and orbit rings in the sky"></div>
    <div class="panel">
      <div class="brand"><span class="brand-dot"></span>Lantern Guild</div>
      <div class="contacts">
        <div>
          <span class="icon"><svg width="14" height="14" viewBox="0 0 24 24"><path d="M12 2a7 7 0 0 0-7 7c0 5 7 13 7 13s7-8 7-13a7 7 0 0 0-7-7zm0 9.5A2.5 2.5 0 1 1 12 6.5a2.5 2.5 0 0 1 0 5z" fill="#1d1d24"/></svg></span>
          <h4>Address</h4><p>12 Orbit Lane, Suite 4<br>Meadowford</p>
        </div>
        <div>
          <span class="icon"><svg width="14" height="14" viewBox="0 0 24 24"><path d="M6.6 10.8a15 15 0 0 0 6.6 6.6l2.2-2.2a1 1 0 0 1 1-.25 11.4 11.4 0 0 0 3.6.57 1 1 0 0 1 1 1V20a1 1 0 0 1-1 1A17 17 0 0 1 3 4a1 1 0 0 1 1-1h3.5a1 1 0 0 1 1 1c0 1.25.2 2.45.57 3.6a1 1 0 0 1-.25 1z" fill="#1d1d24"/></svg></span>
          <h4>Phone</h4><p>+1 555 014 2200</p>
        </div>
        <div>
          <span class="icon"><svg width="14" height="14" viewBox="0 0 24 24"><path d="M3 5h18v14H3z" fill="#1d1d24"/><path d="M3 5l9 7 9-7" fill="none" stroke="#fff" stroke-width="1.6"/></svg></span>
          <h4>Email</h4><p>hello@lanternguildhq.org</p>
        </div>
      </div>
    </div>
    <span class="page-no">6</span>
  </section>

</main>
</body>
</html>
```